New, modern business card for growing audiology practice

We need a new business card for our audiology practice. Our logo and website have recently changed (more modern) and we want our business cards to reflect this change.
We conduct hearing tests, perform earwax removals, and fit & dispense hearing aids to our patients. We are a family owned practice in which the owner is the one who works directly with the patient. I have attached logos in various formats to use, as well as two ideas I found on this website; as well as a scanned copy of our current logo. Good luck!

Industry/Entity Type

Business

Contact Information for Business Card

Company name: Tolvera Hearing Center
Provider name: Peter Wolstenby, Au.D. F/NSB
Phone number: (555) 683-5127
Address: 837 W. Lindell Ave. Harlowe Falls, MN 55972
email: tolverahearing@postvane.com
website: tolverahearing.com

Colors
000000
aaaaaa
dbdbdb
cacaca
9bcb3c
afd23c
cadf82
b1b1b1

Requirements
Must have
• My card must include information in the "details" section. In the attached images, I found a few that I liked and I would like to model after - "brisky bouncin'" and "Sound Method Center".
• Must be horizontal.
• Must include logos provided. I uploaded them in various file formats and various ways.
• Must match logo font, if possible, if not, please get as close as you can.
Nice to have
• I really like the idea of having a color on one side with just the logo and company name and the contact information and provider name on the other side. I also really like the idea of having the main color dominating on the logo/company side with accent of that same color on the contact side of the card.
Should not have
• Must not be vertical.

```html
<!DOCTYPE html>
<html lang="en">
<head>
<meta charset="utf-8">
<title>Tolvera Hearing Center — Business Card</title>
<link rel="stylesheet" href="https://fonts.googleapis.com/css2?family=Open+Sans:wght@400;600;700&display=swap">
<style>
  :root {
    --backdrop: #2b2b2b;
    --card: #0b0b0b;
    --card-edge: #1c1c1c;
    --green: #afd23c;
    --green-deep: #9bcb3c;
    --white: #f2f2f2;
    --grey: #cacaca;
  }
  * { margin: 0; padding: 0; box-sizing: border-box; }
  html, body {
    width: 1200px; height: 873px; overflow: hidden;
    background: var(--backdrop);
    font-family: "Open Sans", Arial, sans-serif;
  }
  .stage {
    position: relative; width: 1200px; height: 873px;
    display: flex; align-items: center; justify-content: center; gap: 40px;
  }
  .card {
    position: relative; width: 540px; height: 309px;
    background: var(--card);
    border: 1px solid var(--card-edge);
    box-shadow: 0 10px 28px rgba(0,0,0,.45);
    color: var(--white);
  }
  .company { font-size: 19px; font-weight: 400; letter-spacing: .3px; text-transform: uppercase; white-space: nowrap; }
  .company .accent { color: var(--green); }

  .card--front .company { position: absolute; left: 28px; top: 26px; }
  .contact { position: absolute; left: 28px; top: 128px; }
  .provider { color: var(--green); font-size: 14px; font-weight: 700; text-transform: uppercase; letter-spacing: .2px; }
  .role { font-size: 12px; color: var(--grey); margin-top: 2px; }
  .address { font-size: 12px; color: var(--grey); margin-top: 14px; line-height: 1.45; }
  .lines { list-style: none; margin-top: 14px; font-size: 12px; color: var(--grey); line-height: 1.55; }
  .lines li { display: flex; align-items: center; gap: 10px; }
  .lines svg { width: 10px; height: 10px; flex: none; }
  .site .accent { color: var(--green); }

  .card--back { display: flex; align-items: center; justify-content: center; }
  .brand { display: flex; align-items: center; gap: 12px; margin-top: -8px; }
  .brand .dot { width: 14px; height: 14px; border-radius: 50%; background: var(--green); }
  .card--back .web {
    position: absolute; left: 0; right: 0; bottom: 26px; text-align: center;
    font-size: 12px; color: var(--grey);
  }
  .card--back .web .accent { color: var(--green); }
</style>
</head>
<body>
<main class="stage">
  <section class="card card--front" aria-label="Contact side">
    <h1 class="company">Tolvera <span class="accent">Hearing</span> Center</h1>
    <div class="contact">
      <p class="provider">Peter Wolstenby, Au.D. F/NSB</p>
      <p class="role">Owner-Audiologist</p>
      <p class="address">837 W. Lindell Ave.<br>Harlowe Falls, MN 55972</p>
      <ul class="lines">
        <li>
          <svg viewBox="0 0 10 10" aria-hidden="true"><path d="M2 1 L4 1 L4.6 3 L3.4 3.8 Q4.4 5.8 6.2 6.6 L7 5.4 L9 6 L9 8 Q5 9.5 1.5 5 Q0.6 3 2 1 Z" fill="var(--green)"/></svg>
          (555) 683-5127
        </li>
        <li>
          <svg viewBox="0 0 10 10" aria-hidden="true"><rect x="0.7" y="2" width="8.6" height="6" fill="none" stroke="var(--green)" stroke-width="1.2"/><path d="M0.7 2 L5 5.4 L9.3 2" fill="none" stroke="var(--green)" stroke-width="1.2"/></svg>
          tolverahearing@postvane.com
        </li>
        <li class="site">
          <svg viewBox="0 0 10 10" aria-hidden="true"><circle cx="5" cy="5" r="4.2" fill="none" stroke="var(--green)" stroke-width="1.1"/><ellipse cx="5" cy="5" rx="1.8" ry="4.2" fill="none" stroke="var(--green)" stroke-width="0.9"/><path d="M0.8 5 H9.2" stroke="var(--green)" stroke-width="0.9"/></svg>
          <span>www.<span class="accent">tolverahearing</span>.com</span>
        </li>
      </ul>
    </div>
  </section>

  <section class="card card--back" aria-label="Brand side">
    <div class="brand">
      <span class="dot" aria-hidden="true"></span>
      <h2 class="company">Tolvera <span class="accent">Hearing</span> Center</h2>
    </div>
    <p class="web">www.<span class="accent">tolverahearing</span>.com</p>
  </section>
</main>
</body>
</html>
```